Website Redesign Brief for Breezeline Climate Services WA

Creating a clear and concise brief for designers to redesign your website, https://breezelineclimatewa.com.au/, is essential to ensure the project aligns with your vision for a more energetic, friendly, optimistic, and user-friendly website. Below is a sample brief tailored to your request, balancing specificity with flexibility to allow designers to bring their creativity to the table.

Website Redesign Brief for Breezeline Climate WA
1. Project Overview

We are seeking a redesign of our website, https://breezelineclimatewa.com.au/, to create a vibrant, engaging, and user-friendly online presence that reflects our brand’s commitment to providing top-notch air conditioning services in Western Australia. The redesigned website should feel energetic, friendly, and optimistic while maintaining professionalism and improving user experience.
2. Goals and Objectives

Enhance Brand Perception: Convey a modern, approachable, and positive brand identity that resonates with both residential and commercial clients.
Improve User Experience: Simplify navigation, improve accessibility, and ensure a seamless experience across devices (desktop, tablet, mobile).
Increase Engagement: Encourage visitors to explore services, request quotes, and contact us through clear calls-to-action (CTAs).
Boost Conversion Rates: Make it easier for users to find information and take action (e.g., booking services or inquiries).
Showcase Expertise: Highlight our professional air conditioning services, experience, and customer satisfaction in an inviting way.

3. Target Audience

Primary Audience: Homeowners and small business owners in Western Australia seeking air conditioning installation, maintenance, or repair services.
Secondary Audience: Property managers, commercial clients, and real estate professionals looking for reliable HVAC solutions.
Demographics: Ages 25–65, mix of tech-savvy and non-tech-savvy users, located primarily in Perth and surrounding areas.
User Needs: Clear information about services, transparent pricing, easy contact options, and reassurance of quality and reliability.

4. Design Preferences

Tone and Style:

Energetic: Use bold, vibrant colors (e.g., blues, whites, and pops of warm tones like orange or yellow) to evoke energy and optimism.
Friendly: Incorporate approachable language, welcoming imagery, and a clean, uncluttered layout.
Optimistic: Highlight positive customer outcomes (e.g., comfort, energy savings) through visuals and messaging.
Professional yet approachable: Maintain credibility as a trusted service provider while avoiding a cold or overly corporate feel.

Visual Elements:

Use high-quality images of happy customers, comfortable homes/offices, and modern air conditioning units.
Incorporate subtle animations or micro-interactions to add energy (e.g., hover effects on buttons or smooth scrolling).
Avoid overly complex graphics that may slow down the site or distract from usability.

Typography: Clean, modern fonts that are easy to read. Use larger, bold headings for hierarchy and warmth.
Inspiration: Websites like https://www.vorlex.com.au/ (clean and professional) or https://www.tandoraclimatech.com.au/ (user-friendly and modern) but with a more vibrant and welcoming vibe.

5. Functional Requirements

User-Friendly Navigation: Simplify the menu structure to make key pages (e.g., Services, About Us, Contact) easily accessible.
Mobile Responsiveness: Ensure the site is fully optimized for mobile devices, with fast load times and intuitive touch interactions.
Key Features:

Prominent CTAs for requesting quotes, booking services, or contacting the team.
A clear service overview with icons or visuals for each service (e.g., installation, repairs, maintenance).
A testimonials section to showcase customer satisfaction.
An easy-to-use contact form with minimal fields.
Integration with Google Maps for location-based services or office directions.

SEO and Performance: Optimize for search engines (e.g., keywords like “air conditioning Perth”) and ensure fast loading speeds.
Accessibility: Follow WCAG guidelines to ensure the site is usable for all visitors, including those with disabilities.

6. Content Guidance

Existing Content: Review and refine current content from https://breezelineclimatewa.com.au/ to make it concise, engaging, and aligned with the friendly tone.
New Content Ideas:

Add a “Why Choose Us” section highlighting expertise, customer service, and eco-friendly solutions.
Include a FAQ page to address common customer questions.
Create a blog section for tips on air conditioning maintenance or energy efficiency (optional).

Tone of Voice: Conversational, reassuring, and positive. Avoid technical jargon unless clearly explained.

7. Technical Considerations

Platform: Open to recommendations (e.g., WordPress, Wix, or custom-built) but prioritize ease of maintenance and scalability.
Integrations: Ensure compatibility with existing tools (e.g., Google Analytics, CRM for quote requests, or booking systems).
Domain and Hosting: Retain current domain (breezelineclimatewa.com.au); hosting recommendations welcome.
Timeline: Initial design concepts within [insert timeline, e.g., 2–3 weeks], with full redesign completed by [insert deadline, e.g., 6–8 weeks].
Budget: [Insert budget range or state “flexible, please provide a quote”].

8. Deliverables

Wireframes and mockups for homepage, service pages, and contact page.
Fully responsive website design with all necessary pages.
Style guide (colors, fonts, imagery guidelines).
CMS setup (if applicable) with basic training for content updates.
Testing and optimization for performance and SEO.

9. Success Metrics

Increased time on site and reduced bounce rate.
Higher conversion rates for quote requests and contact form submissions.
Positive user feedback on ease of navigation and overall experience.
Improved search engine rankings for key terms within [insert timeframe, e.g., 3 months].

10. Additional Notes

Please provide a portfolio of similar projects or examples of user-friendly, vibrant websites.
We are open to creative suggestions to make the website stand out in the HVAC industry.
Regular progress updates and collaboration during the design process are appreciated.
Updates

designers are asking for more time

few have requested an extension. I Have extended

Target Market(s)

Primary Audience: Homeowners and small business owners in Western Australia seeking air conditioning installation, maintenance, or repair services. Secondary Audience: Property managers, commercial clients, and real estate professionals looking for reliable HVAC solutions. Demographics: Ages 25–65, mix of tech-savvy and non-tech-savvy users, located primarily in Perth and surrounding areas. User Needs: Clear information about services, transparent pricing, easy contact options, and reassurance of quality and reliability.

Industry/Entity Type

Air Conditioning and Refrigeration (HVAC & R)

Coding

Coded - Design and coding required

Colors
0054AA
0677BA
7BADD7
CADEEF
E8F1F8
59FF00
82FF00
B8FF75
E3FFCB
F4FFEA
F0912C
F2A743
F7CA91
FBE8D2
FDF5EE
EE7325
F08F49
F5BC92
FAE3D3
FDF4ED

Requirements
Must have
• Must have all my current information I currently have on my web page.
Nice to have
• A sales page for people to buy products online

```html
<!DOCTYPE html>
<html lang="en">
<head>
<meta charset="utf-8">
<title>Breezeline Climate Services WA</title>
<link rel="stylesheet" href="https://fonts.googleapis.com/css2?family=Krona+One&family=Nunito+Sans:wght@400;600;700;800&display=swap">
<style>
:root{
  --navy:#16336b;
  --navy-deep:#0f2a5c;
  --blue:#1f4f93;
  --sky:#7badd7;
  --red:#e3202a;
  --orange:#ee7325;
  --ink:#1b1b24;
  --muted:#4a4f5c;
  --grey-bg:#f1f2f4;
  --footer:#0d111d;
  --white:#ffffff;
}
*{box-sizing:border-box;margin:0;padding:0}
html,body{width:1200px;height:4673px;overflow:hidden}
body{font-family:"Nunito Sans",sans-serif;color:var(--ink);background:var(--white);position:relative}
.section{position:absolute;left:0;width:1200px;overflow:hidden}
.heading{font-family:"Krona One",sans-serif;font-size:27px;text-transform:uppercase;letter-spacing:1px;color:var(--ink);text-align:center;position:absolute;left:0;width:100%}
.heading .accent{color:var(--red)}
.heading-mark{position:absolute;width:60px;height:4px;border-radius:2px;background:linear-gradient(90deg,var(--navy),var(--orange))}
.btn{position:absolute;display:flex;align-items:center;justify-content:center;border-radius:24px;color:var(--white);font-weight:800;font-size:12px;text-transform:uppercase;letter-spacing:.3px}
.btn-red{background:linear-gradient(90deg,var(--red),var(--orange))}
.btn-navy{background:var(--navy)}
.photo{position:absolute}

/* top bar & header */
.topbar{position:absolute;left:400px;top:0;width:800px;height:38px;background:linear-gradient(90deg,var(--red),var(--orange));border-bottom-left-radius:22px;display:flex;align-items:center;justify-content:space-around;padding-left:30px;color:var(--white);font-size:12.5px;font-weight:700}
.topbar span{display:flex;align-items:center;gap:6px}
.brand{position:absolute;left:105px;top:48px;display:flex;align-items:center;gap:10px}
.brand-dot{width:34px;height:34px;border-radius:50%;background:var(--red)}
.brand-name{font-size:15px;font-weight:800;color:var(--navy);line-height:1.15;width:150px}
.nav{position:absolute;left:343px;top:76px;font-size:12px;font-weight:700;color:var(--ink);text-transform:uppercase}
.nav a{color:inherit;text-decoration:none}
.nav .active{color:var(--red)}
.nav i{font-style:normal;margin:0 6px;color:#555}

/* hero */
.hero{top:125px;height:538px}
.hero .photo{left:0;top:0;width:1200px;height:538px;background:linear-gradient(120deg,#cfd8c6,#e9e5dc 45%,#b9c9a7 80%,#8ea87a)}
.hero-title{position:absolute;left:110px;top:98px;font-family:"Krona One",sans-serif;font-size:25px;line-height:33px;color:var(--white);text-transform:uppercase}
.hero-title .light{color:var(--sky)}
.hero-text{position:absolute;left:110px;top:252px;width:420px;color:var(--white);font-size:13.5px;line-height:27px}

/* services */
.services{top:663px;height:682px;background:var(--white)}
.intro{position:absolute;left:250px;width:700px;text-align:center;font-size:13.5px;line-height:26px;color:var(--muted)}
.card{position:absolute;top:217px;width:312px;height:348px;background:var(--white);border-radius:8px;box-shadow:0 6px 24px rgba(0,0,0,.09);text-align:center}
.card .photo{left:10px;top:8px;width:292px;height:205px;border-radius:4px}
.card h3{position:absolute;left:0;top:232px;width:100%;font-size:13.5px;font-weight:800;text-transform:uppercase}
.card p{position:absolute;top:254px;left:36px;width:240px;font-size:12.5px;line-height:23px;color:var(--muted)}
.card .more{position:absolute;left:0;top:318px;width:100%;display:block;text-align:center;font-size:12.5px;font-weight:800;color:var(--red);text-transform:uppercase}
.arrow{position:absolute;width:40px;height:40px;border-radius:50%;display:flex;align-items:center;justify-content:center;font-weight:800;font-size:16px}
.arrow.light{background:var(--white);box-shadow:0 2px 10px rgba(0,0,0,.12);color:var(--ink)}
.arrow.dark{background:var(--navy);color:var(--white)}

/* about */
.about{top:1345px;height:593px;background:var(--grey-bg)}
.about .photo{left:115px;top:90px;width:425px;height:425px;border-radius:50%;background:linear-gradient(160deg,#7d9a6b,#a7b693 40%,#2a3b5e 75%,#1c2b48)}
.about-title{position:absolute;left:642px;top:125px;font-family:"Krona One",sans-serif;font-size:27px;text-transform:uppercase}
.about-title .accent{color:var(--red)}
.about-copy{position:absolute;left:642px;top:172px;width:440px;font-size:13.5px;line-height:26.5px;color:var(--muted)}
.about-copy p+p{margin-top:18px}

/* why choose */
.why{top:1938px;height:444px;background:linear-gradient(100deg,#d9192a,#e83a27 50%,#ee7325)}
.why .heading{color:var(--white)}
.feature{position:absolute;top:185px;display:flex;gap:14px;color:var(--white)}
.feature-icon{width:80px;height:80px;border-radius:50%;background:var(--white);flex:none;display:flex;align-items:center;justify-content:center}
.feature h4{font-size:14.5px;font-weight:800;margin-top:10px}
.feature p{font-size:12.5px;line-height:22px;margin-top:8px;width:260px;opacity:.95}

/* testimonials */
.testimonials{top:2382px;height:466px;background:var(--white)}
.tcard{position:absolute;top:200px;width:312px;height:184px;border-radius:6px;background:var(--white);box-shadow:0 6px 24px rgba(0,0,0,.08);padding:28px 22px 0 22px;font-size:12.3px;line-height:23px;color:var(--muted)}
.tcard.featured{background:var(--navy);color:var(--white)}
.tname{font-size:11.5px;font-weight:800;text-transform:uppercase;color:var(--ink);display:flex;gap:14px;margin-bottom:8px}
.tcard.featured .tname{color:var(--white)}
.stars{color:var(--orange);letter-spacing:2px}
.quote-badge{position:absolute;top:-20px;right:22px;width:44px;height:44px;border-radius:50%;background:linear-gradient(135deg,var(--red),var(--orange));color:var(--white);font-family:Georgia,serif;font-size:34px;line-height:56px;text-align:center}

/* brands */
.brands{top:2848px;height:312px;background:var(--grey-bg)}
.brand-name-logo{position:absolute;top:190px;font-size:24px;font-weight:800;text-transform:uppercase}

/* faq */
.faq{top:3160px;height:537px;background:var(--white)}
.faq-item{position:absolute;left:298px;width:604px;height:52px;border-radius:26px;background:var(--white);box-shadow:0 4px 18px rgba(0,0,0,.08);display:flex;align-items:center;justify-content:space-between;padding:0 18px 0 30px;font-size:12.5px;font-weight:800;text-transform:uppercase}
.faq-toggle{width:34px;height:34px;border-radius:50%;background:linear-gradient(135deg,var(--red),var(--orange));color:var(--white);display:flex;align-items:center;justify-content:center;font-size:13px}

/* contact */
.contact{top:3697px;height:535px}
.contact .photo{left:0;top:0;width:1200px;height:535px;background:linear-gradient(100deg,#6b5a4c,#a99a88 35%,#d9d5cf 60%,#c9cbce)}
.contact-title{position:absolute;left:710px;top:90px;font-family:"Krona One",sans-serif;font-size:25px;color:var(--white);text-transform:uppercase}
.field{position:absolute;left:710px;width:378px;background:var(--white);border-radius:22px;font-size:12.5px;font-weight:700;color:var(--ink);padding:0 22px;display:flex;align-items:center;text-transform:uppercase}

/* footer */
.footer{top:4232px;height:441px;background:var(--footer);color:var(--white)}
.social{position:absolute;top:108px;left:114px;display:flex;gap:6px}
.social span{width:34px;height:34px;border-radius:50%;background:var(--white)}
.footer-brand{position:absolute;left:500px;top:90px;width:200px;display:flex;flex-direction:column;align-items:center;gap:8px}
.footer-brand .brand-name{color:var(--white);text-align:center;width:200px}
.footer-nav{position:absolute;top:215px;left:0;width:100%;text-align:center;font-size:12px;font-weight:800;text-transform:uppercase}
.footer-nav i{font-style:normal;margin:0 5px}
.footer-rule{position:absolute;left:210px;top:246px;width:780px;height:1px;background:rgba(255,255,255,.3)}
.footer-contact{position:absolute;top:266px;left:0;width:100%;display:flex;justify-content:center;gap:50px;font-size:12.5px;font-weight:700}
.footer-contact span{display:flex;align-items:center;gap:6px}
.copyright{position:absolute;top:322px;left:0;width:100%;text-align:center;font-size:12.5px}
</style>
</head>
<body>

<header>
  <div class="topbar">
    <span><svg width="11" height="14" viewBox="0 0 11 14"><path d="M5.5 0A5.5 5.5 0 0 0 0 5.5C0 9.6 5.5 14 5.5 14S11 9.6 11 5.5A5.5 5.5 0 0 0 5.5 0Zm0 7.6a2.1 2.1 0 1 1 0-4.2 2.1 2.1 0 0 1 0 4.2Z" fill="#fff"/></svg>42 Larkspur Lane, Wattleup WA 6166</span>
    <span><svg width="14" height="11" viewBox="0 0 14 11"><rect x=".7" y=".7" width="12.6" height="9.6" rx="1.5" fill="none" stroke="#fff" stroke-width="1.4"/><path d="M1 1.5 7 6l6-4.5" fill="none" stroke="#fff" stroke-width="1.4"/></svg>info@breezelineclimatewa.com.au</span>
    <span><svg width="13" height="13" viewBox="0 0 13 13"><path d="M3 .5 5 3 3.8 4.6a8 8 0 0 0 4.6 4.6L10 8l2.5 2-1.2 2.2C5.6 12.5.5 7.4.8 1.7Z" fill="#fff"/></svg>0400 555 218</span>
  </div>
  <div class="brand">
    <span class="brand-dot"></span>
    <span class="brand-name">Breezeline Climate Services WA</span>
  </div>
  <nav class="nav">
    <a class="active">Home</a><i>|</i><a>About Us</a><i>|</i><a>Services</a><i>|</i><a>Cleaning</a><i>|</i><a>Regasing</a><i>|</i><a>Commissioning</a><i>|</i><a>Air Balancing</a>
  </nav>
  <div class="btn btn-navy" style="left:930px;top:63px;width:158px;height:45px">Request a Quote</div>
</header>

<section class="section hero">
  <div class="photo" role="img" aria-label="Smiling family relaxing together on a sofa in a cool, bright living room"></div>
  <svg style="position:absolute;left:0;top:0" width="700" height="538" viewBox="0 0 700 538" aria-hidden="true">
    <defs><linearGradient id="heroBlue" x1="0" y1="0" x2="1" y2="1"><stop offset="0" stop-color="#0f2a5c"/><stop offset="1" stop-color="#1f4f93"/></linearGradient></defs>
    <path d="M0 0H560C680 120 650 410 440 538H0Z" fill="url(#heroBlue)"/>
  </svg>
  <h1 class="hero-title">Quality <span class="light">Air<br>Conditioning</span><br>Repairs, Service &amp;<br>Installations</h1>
  <p class="hero-text">Our service is second to none; we have a team of experienced technicians that consistently deliver the best quality air conditioner repairs Perth has to offer.</p>
  <div class="btn btn-red" style="left:109px;top:363px;width:157px;height:44px">Book a Service</div>
</section>

<section class="section services">
  <span class="heading-mark" style="left:570px;top:78px"></span>
  <h2 class="heading" style="top:95px">Our <span class="accent">Services</span></h2>
  <p class="intro" style="top:138px">Please Be aware that paying for your service upfront does not mean next day service. Your service will however be prioritised and scheduled into the next available slot.</p>
  <div class="arrow light" style="left:48px;top:369px">«</div>
  <article class="card" style="left:110px">
    <div class="photo" role="img" aria-label="Technician installing an outdoor air conditioning unit on a house wall" style="background:linear-gradient(150deg,#5f93d1,#9cc1e6 45%,#b88a4c 75%,#55422f)"></div>
    <h3>Installation</h3>
    <p>Lorem ipsum dolor sit amet, consectetur adipiscing elit, sed do</p>
    <span class="more">View More</span>
  </article>
  <article class="card" style="left:443px">
    <div class="photo" role="img" aria-label="Technician repairing an indoor split system unit" style="background:linear-gradient(150deg,#e9ecef,#cfd5dc 50%,#e16a2a 80%,#2c4d8a)"></div>
    <h3>Repairs</h3>
    <p>Lorem ipsum dolor sit amet, consectetur adipiscing elit, sed do</p>
    <span class="more">View More</span>
  </article>
  <article class="card" style="left:775px">
    <div class="photo" role="img" aria-label="Modern living room with cool air flowing from a wall unit" style="background:linear-gradient(150deg,#3e4550,#7a8694 45%,#8fd0f2 70%,#c9ccd0)"></div>
    <h3>Maintenance</h3>
    <p>Lorem ipsum dolor sit amet, consectetur adipiscing elit, sed do</p>
    <span class="more">View More</span>
  </article>
  <div class="arrow dark" style="left:1106px;top:369px">»</div>
</section>

<section class="section about">
  <div class="photo" role="img" aria-label="Friendly technician standing in front of a family home with the owners behind him"></div>
  <span class="heading-mark" style="left:645px;top:105px"></span>
  <h2 class="about-title">About <span class="accent">Us</span></h2>
  <div class="about-copy">
    <p>Our service is second to none; our team of experienced technicians that consistently deliver the best quality air conditioner repairs Perth has to offer. There are many different brands of air conditioning on the market, each with their own way of controlling the temperature of your home.</p>
    <p>Our service is second to none; our team of experienced technicians that consistently deliver the best quality air conditioner repairs Perth has to offer.</p>
  </div>
  <div class="btn btn-red" style="left:642px;top:430px;width:158px;height:44px">Learn More</div>
</section>

<section class="section why">
  <span class="heading-mark" style="left:570px;top:85px;background:#fff"></span>
  <h2 class="heading" style="top:100px">Why Choose Us</h2>
  <div class="feature" style="left:32px">
    <div class="feature-icon"><svg width="42" height="42" viewBox="0 0 42 42" fill="none" stroke="#16336b" stroke-width="2"><circle cx="21" cy="16" r="12"/><path d="M21 9l2.2 4.5 5 .7-3.6 3.5.9 5-4.5-2.4-4.5 2.4.9-5-3.6-3.5 5-.7Z"/><path d="M13 25 9 38l6-3 3 5 3-9M29 25l4 13-6-3-3 5-3-9"/></svg></div>
    <div><h4>Experts in Air Conditioning</h4><p>Lorem ipsum dolor sit amet, consectetur adipiscing elit, sed do eiusmod</p></div>
  </div>
  <div class="feature" style="left:422px">
    <div class="feature-icon"><svg width="42" height="42" viewBox="0 0 42 42" fill="none" stroke="#16336b" stroke-width="2"><circle cx="21" cy="21" r="18"/><circle cx="17" cy="15" r="5"/><path d="M8 31c2-6 6-8 9-8s5 1 6 2"/><circle cx="29" cy="28" r="7"/><path d="m26 28 2 2 4-4"/></svg></div>
    <div><h4>Specialist Dealer Network</h4><p>Lorem ipsum dolor sit amet, consectetur adipiscing elit, sed do eiusmod</p></div>
  </div>
  <div class="feature" style="left:812px">
    <div class="feature-icon"><svg width="42" height="42" viewBox="0 0 42 42" fill="none" stroke="#16336b" stroke-width="2"><circle cx="21" cy="21" r="13"/><circle cx="21" cy="21" r="5"/><path d="M21 3v5M21 34v5M3 21h5M34 21h5M8 8l4 4M30 30l4 4M34 8l-4 4M12 30l-4 4"/></svg></div>
    <div><h4>Quality After Sales Support</h4><p>Lorem ipsum dolor sit amet, consectetur adipiscing elit, sed do eiusmod</p></div>
  </div>
  <div class="btn btn-navy" style="left:521px;top:320px;width:158px;height:42px">Request a Quote</div>
</section>

<section class="section testimonials">
  <span class="heading-mark" style="left:570px;top:105px"></span>
  <h2 class="heading" style="top:122px">Our <span class="accent">Testimonials</span></h2>
  <div class="arrow light" style="left:48px;top:272px;box-shadow:none">«</div>
  <article class="tcard" style="left:115px">
    <span class="quote-badge">”</span>
    <div class="tname">Jordan Miles <span class="stars">★★★★★</span></div>
    Please thank Liam for his professionalism and honesty. He advised us that a service was not required after checking over everything and fixed other items.
  </article>
  <article class="tcard featured" style="left:445px">
    <span class="quote-badge">”</span>
    <div class="tname">Jordan Miles <span class="stars">★★★★★</span></div>
    Thank you Liam and Marco for installing our 18kW unit. My brother is a fridgy tech and looked over the install for me. I said its near perfect. Thank you.
  </article>
  <article class="tcard" style="left:775px">
    <span class="quote-badge">”</span>
    <div class="tname">Jordan Miles <span class="stars">★★★★★</span></div>
    Liam, thank you for fixing my mums aircon and helping us with the insurance claim. Above and beyond. I appreciate it.
  </article>
  <div class="arrow dark" style="left:1106px;top:272px">»</div>
</section>

<section class="section brands">
  <span class="heading-mark" style="left:570px;top:75px"></span>
  <h2 class="heading" style="top:92px">Our Recommended <span class="accent">Brands</span></h2>
  <span class="brand-name-logo" style="left:150px;color:#d21f2a;font-size:19px">Tandora Climatech</span>
  <span class="brand-name-logo" style="left:402px;color:#2b6fb6;font-size:19px">Coolridge Intl</span>
  <span class="brand-name-logo" style="left:630px;color:#1a5eb4">Vorlex</span>
  <span class="brand-name-logo" style="left:864px;color:#1f3f78">Ventara</span>
</section>

<section class="section faq">
  <span class="heading-mark" style="left:570px;top:88px"></span>
  <h2 class="heading" style="top:105px">Any Question <span class="accent">Ask Me</span></h2>
  <div class="faq-item" style="top:187px">1. Lorum ipsum dolor sit amet to lorum ipsum ?<span class="faq-toggle">»</span></div>
  <div class="faq-item" style="top:254px">2. Lorum ipsum dolor sit amet to lorum ipsum ?<span class="faq-toggle">»</span></div>
  <div class="faq-item" style="top:321px">3. Lorum ipsum dolor sit amet to lorum ipsum ?<span class="faq-toggle">»</span></div>
  <div class="faq-item" style="top:388px">4. Lorum ipsum dolor sit amet to lorum ipsum ?<span class="faq-toggle">»</span></div>
</section>

<section class="section contact">
  <div class="photo" role="img" aria-label="Cheerful technician servicing a wall-mounted air conditioner"></div>
  <svg style="position:absolute;right:0;top:0" width="640" height="535" viewBox="0 0 640 535" aria-hidden="true">
    <defs><linearGradient id="contactBlue" x1="0" y1="0" x2="1" y2="1"><stop offset="0" stop-color="#1f4f93"/><stop offset="1" stop-color="#0f2a5c"/></linearGradient></defs>
    <path d="M640 0H130C10 110 0 400 120 535H640Z" fill="url(#contactBlue)"/>
  </svg>
  <span class="heading-mark" style="left:712px;top:70px;background:#fff"></span>
  <h2 class="contact-title">Get In Touch</h2>
  <div class="field" style="top:143px;height:56px">Name</div>
  <div class="field" style="top:210px;height:56px">Email</div>
  <div class="field" style="top:276px;height:122px;align-items:flex-start;padding-top:18px">Message</div>
  <div class="btn btn-red" style="left:714px;top:405px;width:158px;height:42px">Submit</div>
</section>

<footer class="section footer">
  <div class="social" role="img" aria-label="Social media links"><span></span><span></span><span></span></div>
  <div class="footer-brand"><span class="brand-dot"></span><span class="brand-name">Breezeline Climate Services WA</span></div>
  <div class="btn btn-red" style="left:928px;top:100px;width:158px;height:44px">View Map</div>
  <nav class="footer-nav">Home<i>|</i>About Us<i>|</i>Services<i>|</i>Cleaning<i>|</i>Regasing<i>|</i>Commissioning<i>|</i>Air Balancing<i>|</i>Contact Us</nav>
  <div class="footer-rule"></div>
  <div class="footer-contact">
    <span><svg width="11" height="14" viewBox="0 0 11 14"><path d="M5.5 0A5.5 5.5 0 0 0 0 5.5C0 9.6 5.5 14 5.5 14S11 9.6 11 5.5A5.5 5.5 0 0 0 5.5 0Zm0 7.6a2.1 2.1 0 1 1 0-4.2 2.1 2.1 0 0 1 0 4.2Z" fill="#fff"/></svg>42 Larkspur Lane, Wattleup WA 6166</span>
    <span><svg width="14" height="11" viewBox="0 0 14 11"><rect x=".7" y=".7" width="12.6" height="9.6" rx="1.5" fill="none" stroke="#fff" stroke-width="1.4"/><path d="M1 1.5 7 6l6-4.5" fill="none" stroke="#fff" stroke-width="1.4"/></svg>info@breezelineclimatewa.com.au</span>
    <span><svg width="13" height="13" viewBox="0 0 13 13"><path d="M3 .5 5 3 3.8 4.6a8 8 0 0 0 4.6 4.6L10 8l2.5 2-1.2 2.2C5.6 12.5.5 7.4.8 1.7Z" fill="#fff"/></svg>0400 555 218</span>
  </div>
  <p class="copyright">Copyright@2025.All Rights Reserved</p>
</footer>

</body>
</html>
```